I need a business card design for a new business based in South West Australia.
I specialize in residential window cleaning & general handyman maintenance.

Dale Marsh - 412 SILVER HAWK DETAILING
- Window Cleaning
- House Maintenance

```html
<!DOCTYPE html>
<html lang="en">
<head>
<meta charset="utf-8">
<title>412 Silver Hawk Detailing – Business Card</title>
<link href="https://fonts.googleapis.com/css2?family=Open+Sans:wght@400;600&display=swap" rel="stylesheet">
<style>
  :root {
    --page-bg: #e9e6e1;
    --blue-light: #3a9be0;
    --blue-mid: #1f7fcc;
    --blue-deep: #0d5fae;
    --band-grey: #8c9096;
    --edge-white: #ffffff;
    --photo-light: #b9cfe3;
    --photo-mid: #7f9fbf;
    --photo-dark: #4f6e90;
    --text-white: #ffffff;
  }
  html, body {
    margin: 0;
    padding: 0;
    width: 1200px;
    height: 892px;
    overflow: hidden;
    background: var(--page-bg);
  }
  .card {
    position: absolute;
    left: 100px;
    top: 160px;
    width: 1000px;
    height: 572px;
    overflow: hidden;
    box-shadow: 0 10px 30px rgba(0,0,0,0.18);
    font-family: "Open Sans", sans-serif;
    color: var(--text-white);
  }
  .card-art {
    position: absolute;
    inset: 0;
    width: 1000px;
    height: 572px;
  }
  .company-name {
    position: absolute;
    right: 45px;
    top: 105px;
    margin: 0;
    font-size: 25px;
    font-weight: 400;
    letter-spacing: 0.3px;
    white-space: nowrap;
    text-transform: uppercase;
  }
  .owner-name {
    position: absolute;
    right: 75px;
    top: 185px;
    margin: 0;
    font-size: 38px;
    font-weight: 600;
    white-space: nowrap;
  }
  .services {
    position: absolute;
    right: 45px;
    top: 320px;
    margin: 0;
    padding: 0;
    list-style: none;
    text-align: right;
    font-size: 26px;
    line-height: 54px;
    white-space: nowrap;
  }
  .services li::after {
    content: "";
    display: inline-block;
    width: 10px;
    height: 10px;
    margin-left: 18px;
    border-radius: 50%;
    background: var(--text-white);
    vertical-align: middle;
  }
</style>
</head>
<body>
  <div class="card">
    <svg class="card-art" viewBox="0 0 1000 572" xmlns="http://www.w3.org/2000/svg">
      <defs>
        <linearGradient id="blueField" x1="0" y1="0" x2="1" y2="1">
          <stop offset="0" stop-color="var(--blue-light)"/>
          <stop offset="0.55" stop-color="var(--blue-mid)"/>
          <stop offset="1" stop-color="var(--blue-deep)"/>
        </linearGradient>
        <linearGradient id="photoTones" x1="0" y1="0" x2="1" y2="1">
          <stop offset="0" stop-color="var(--photo-light)"/>
          <stop offset="0.5" stop-color="var(--photo-mid)"/>
          <stop offset="1" stop-color="var(--photo-dark)"/>
        </linearGradient>
      </defs>
      <rect class="blue-field" width="1000" height="572" fill="url(#blueField)"/>
      <path class="grey-band" transform="translate(20 0)"
            d="M0,0 H640 C560,120 470,160 450,300 C430,430 480,500 430,572 H0 Z"
            fill="var(--band-grey)"/>
      <path class="white-edge" transform="translate(20 0)"
            d="M640,0 C560,120 470,160 450,300 C430,430 480,500 430,572"
            fill="none" stroke="var(--edge-white)" stroke-width="8"/>
      <path class="photo-area" role="img" transform="translate(-35 0)"
            aria-label="Photo of a window cleaner in a lift basket working on a glass building facade"
            d="M0,0 H640 C560,120 470,160 450,300 C430,430 480,500 430,572 H0 Z"
            fill="url(#photoTones)"/>
    </svg>
    <h1 class="company-name">412 Silver Hawk Detailing</h1>
    <p class="owner-name">Dale Marsh</p>
    <ul class="services">
      <li>House Maintenance</li>
      <li>Window Cleaning</li>
    </ul>
  </div>
</body>
</html>
```